Harborline Auto LLC

Car Dealer Customer Service
Address: 2874 Cresthaven Road, Larkmoor, VT 05491
web: www.harborlineautoxq.net
email: harborlineautoxq@mailnest.example
Phone: (555) 555-0148
Phone: (555) 555-0173

```html
<!DOCTYPE html>
<html lang="en">
<head>
<meta charset="utf-8">
<title>Harborline Auto – Business Card</title>
<link rel="stylesheet" href="https://fonts.googleapis.com/css2?family=Poppins:wght@400;600;700&display=swap">
<style>
  :root {
    --backdrop: #2b2b2b;
    --card: #f2f2f2;
    --brand-blue: #1c76a8;
    --brand-gold: #e2a53a;
    --ink: #232323;
  }
  * { margin: 0; padding: 0; box-sizing: border-box; }
  html, body { width: 1200px; height: 1138px; overflow: hidden; }
  body {
    background: var(--backdrop);
    font-family: "Poppins", sans-serif;
    color: var(--ink);
    position: relative;
  }
  .card {
    position: absolute;
    background: var(--card);
    border-radius: 16px;
    overflow: hidden;
  }
  /* Front */
  .card-front { left: 274px; top: 186px; width: 622px; height: 376px; }
  .front-brand {
    position: absolute; left: 0; right: 0; top: 218px;
    display: flex; justify-content: center; align-items: center; gap: 14px;
  }
  .brand-dot { width: 22px; height: 22px; border-radius: 50%; background: var(--brand-gold); }
  .front-name {
    font-weight: 700; font-size: 29px; letter-spacing: 0.5px;
    color: var(--brand-blue); line-height: 1;
  }
  .front-web {
    position: absolute; left: 0; right: 0; top: 322px;
    display: flex; justify-content: center; align-items: center; gap: 22px;
    font-size: 15px;
  }
  .front-web .rule { width: 52px; height: 2px; background: var(--brand-gold); }
  .front-band { position: absolute; left: 0; bottom: 0; width: 100%; height: 18px; display: flex; }
  .front-band .band-blue { width: 50%; background: var(--brand-blue); }
  .front-band .band-gold { width: 50%; background: var(--brand-gold); }

  /* Back */
  .card-back { left: 275px; top: 608px; width: 619px; height: 374px; }
  .back-panel { position: absolute; left: 0; top: 0; }
  .back-name {
    position: absolute; left: 0; width: 300px; top: 252px; text-align: center;
    font-weight: 700; font-size: 23px; letter-spacing: 0.5px; color: #fff; white-space: nowrap;
  }
  .contact { position: absolute; right: 24px; text-align: right; }
  .person-name { top: 46px; font-weight: 700; font-size: 24px; color: var(--brand-blue); line-height: 1.2; }
  .person-role { top: 76px; font-size: 16px; }
  .address { top: 204px; font-size: 16px; line-height: 22px; }
  .lines { position: absolute; right: 24px; top: 258px; }
  .line {
    display: flex; justify-content: flex-end; align-items: center; gap: 10px;
    height: 22px; font-size: 16px; white-space: nowrap;
  }
  .line.phone { font-weight: 600; color: var(--brand-blue); font-size: 17px; }
  .line.email { font-size: 15px; }
  .line svg { width: 14px; height: 14px; flex: none; }
</style>
</head>
<body>

<section class="card card-front" aria-label="Card front">
  <div class="front-brand">
    <span class="brand-dot"></span>
    <span class="front-name">HARBORLINE AUTO</span>
  </div>
  <div class="front-web">
    <span class="rule"></span>
    <span>www.harborlineautoxq.net</span>
    <span class="rule"></span>
  </div>
  <div class="front-band"><span class="band-blue"></span><span class="band-gold"></span></div>
</section>

<section class="card card-back" aria-label="Card back">
  <svg class="back-panel" width="330" height="374" viewBox="0 0 330 374">
    <path d="M0 0 H242 Q368 187 248 374 H0 Z" fill="var(--brand-gold)"/>
    <path d="M0 0 H230 Q354 187 236 374 H0 Z" fill="var(--brand-blue)"/>
  </svg>
  <div class="back-name">HARBORLINE AUTO</div>

  <div class="contact person-name">Dorian Keller</div>
  <div class="contact person-role">Managing Director</div>
  <div class="contact address">2874 Cresthaven Road,<br>Larkmoor, VT 05491</div>

  <div class="lines">
    <div class="line phone">(555) 555-0148
      <svg viewBox="0 0 16 16"><path d="M1 6 Q8 0 15 6 L15 8 L11.5 8 L11 6 Q8 5 5 6 L4.5 8 L1 8 Z M4 9 L6 7.5 H10 L12 9 L13 14 H3 Z" fill="var(--brand-gold)"/></svg>
    </div>
    <div class="line phone">(555) 555-0173
      <svg viewBox="0 0 16 16"><path d="M1 6 Q8 0 15 6 L15 8 L11.5 8 L11 6 Q8 5 5 6 L4.5 8 L1 8 Z M4 9 L6 7.5 H10 L12 9 L13 14 H3 Z" fill="var(--brand-gold)"/></svg>
    </div>
    <div class="line">www.harborlineautoxq.net
      <svg viewBox="0 0 16 16"><g fill="none" stroke="var(--brand-gold)" stroke-width="1.5"><circle cx="8" cy="8" r="6.5"/><ellipse cx="8" cy="8" rx="3" ry="6.5"/><path d="M1.5 8 H14.5"/></g></svg>
    </div>
    <div class="line email">harborlineautoxq@mailnest.example
      <svg viewBox="0 0 16 16"><rect x="1" y="3" width="14" height="10" fill="var(--brand-gold)"/><path d="M1 3 L8 9 L15 3" fill="none" stroke="#fff" stroke-width="1.2"/></svg>
    </div>
  </div>
</section>

</body>
</html>
```